Improved Business Card, Government Contracting

We are looking to update the design of our business cards. We would like to create a template that can be used for future employees and easy to update.

Halvorsen Advisory Partners, LLC is a Service Disabled Veteran Owned Small Business with headquarters located in Millbrook, NE. Our current website is www.hvadpt.com. We have contracts in KS and VA with expansion opportunities in various other states. Our primary line of work is within government contracting and providing consulting services to various organizations within the Bureau of Civic Readiness. We would like to project a professional image of our company that is consistent with the industry. Provided are previous versions of our business card template that shows our logo as well. We would like to make sure the information on the cards are easily noticeable .

Target Market(s)

Government Officials
Fellow Small Business Contractors
Large Business Contractors (ex. TQLB, Pellwick Darrow, Fenwey Marsh Colquitt)

Industry/Entity Type

Business

Contact Information for Business Card

Dale Forsyth
Office Manager
Halvorsen Advisory Partners
Ph: 555.204.7716
Email: d.forsyth@hvadpt.us
www.hvadpt.com

Requirements
Must have
• The business mailing address is:
• 48730 212th Crescent
• Millbrook, NE 66091
Nice to have
• Embossed lettering

```html
<!DOCTYPE html>
<html lang="en">
<head>
<meta charset="utf-8">
<title>Halvorsen Advisory Partners – Business Card</title>
<link href="https://fonts.googleapis.com/css2?family=Lato:wght@400;700;900&display=swap" rel="stylesheet">
<style>
  :root {
    --brand-blue: #2f2c9f;
    --brand-navy: #26237a;
    --brand-yellow: #f7ec3c;
    --card-white: #ffffff;
    --backdrop: #e9e9ec;
    --text-light: #ffffff;
  }
  * { margin: 0; padding: 0; box-sizing: border-box; }
  html, body {
    width: 1200px; height: 835px; overflow: hidden;
    background: var(--backdrop);
    font-family: "Lato", sans-serif;
  }
  .sheet {
    position: relative; width: 1200px; height: 835px;
    display: flex; align-items: center; justify-content: center; gap: 50px;
  }
  .card {
    position: relative; width: 525px; height: 300px;
    border-radius: 18px; overflow: hidden;
    background: var(--card-white);
    box-shadow: 0 6px 18px rgba(0,0,0,0.15);
  }

  /* Front */
  .card-front {
    display: flex; flex-direction: column; align-items: center;
    justify-content: center; text-align: center; color: var(--brand-navy);
  }
  .brand-mark {
    display: flex; align-items: center; gap: 10px;
    font-size: 26px; font-weight: 900; color: var(--brand-blue);
    margin-bottom: 14px;
  }
  .brand-mark .mark-square {
    width: 22px; height: 22px; background: var(--brand-yellow);
  }
  .company-name {
    font-size: 18px; font-weight: 900; margin-bottom: 16px;
  }
  .services { list-style: none; font-size: 14px; font-weight: 700; line-height: 1.25; }

  /* Back */
  .card-back { background: var(--brand-blue); }
  .back-shape { position: absolute; inset: 0; }
  .back-brand {
    position: absolute; left: 30px; top: 118px; width: 190px;
    font-size: 20px; font-weight: 700; line-height: 1.15;
    color: var(--brand-blue); text-align: center;
  }
  .contact {
    position: absolute; right: 28px; top: 26px;
    text-align: right; color: var(--text-light);
  }
  .contact-name { font-size: 22px; font-weight: 900; color: var(--brand-yellow); }
  .contact-title { font-size: 16px; margin-bottom: 20px; }
  .contact-line {
    display: flex; justify-content: flex-end; align-items: center; gap: 7px;
    font-size: 16px; line-height: 1.35;
  }
  .contact-line svg { width: 13px; height: 13px; }
  .address { margin-top: 20px; font-size: 16px; line-height: 1.35; }
</style>
</head>
<body>
<main class="sheet">

  <section class="card card-front" aria-label="Business card front">
    <div class="brand-mark"><span class="mark-square"></span>Halvorsen Advisory Partners</div>
    <h1 class="company-name">Halvorsen Advisory Partners</h1>
    <ul class="services">
      <li>Software &amp; Systems Engineering</li>
      <li>Decision Analysis &amp; Process Improvement</li>
      <li>Program &amp; Budget Analysis</li>
      <li>Command and Control</li>
      <li>Program Management</li>
    </ul>
  </section>

  <section class="card card-back" aria-label="Business card back">
    <svg class="back-shape" viewBox="0 0 525 300" preserveAspectRatio="none">
      <polygon points="0,0 102,0 300,140 152,300 0,300" fill="var(--brand-yellow)"/>
      <polygon points="0,0 90,0 283,140 140,300 0,300" fill="var(--card-white)"/>
    </svg>
    <div class="back-brand">Halvorsen<br>Advisory Partners</div>
    <div class="contact">
      <div class="contact-name">Dale Forsyth</div>
      <div class="contact-title">Office Manager</div>
      <div class="contact-line">555.204.7716
        <svg viewBox="0 0 16 16"><path d="M3 1h3l1 4-2 1c1 2 3 4 5 5l1-2 4 1v3c0 1-1 2-2 2C7 15 1 9 1 3c0-1 1-2 2-2z" fill="var(--brand-yellow)"/></svg>
      </div>
      <div class="contact-line">d.forsyth@hvadpt.us
        <svg viewBox="0 0 16 16"><rect x="1" y="3" width="14" height="10" fill="var(--brand-yellow)"/><path d="M1 3l7 6 7-6" fill="none" stroke="var(--brand-blue)" stroke-width="1.4"/></svg>
      </div>
      <div class="contact-line">www.hvadpt.com
        <svg viewBox="0 0 16 16"><circle cx="8" cy="8" r="7" fill="var(--brand-yellow)"/><g fill="none" stroke="var(--brand-blue)" stroke-width="1"><ellipse cx="8" cy="8" rx="3" ry="7"/><path d="M1 8h14M2.5 4.5h11M2.5 11.5h11"/></g></svg>
      </div>
      <div class="address">48730 212th Crescent<br>Millbrook, NE 66091</div>
    </div>
  </section>

</main>
</body>
</html>
```